Business Card Design

I already have a company logo for my company. I have a logo for the manufacturer we represent. I want a professional business card design.

```html
<!DOCTYPE html>
<html lang="en">
<head>
<meta charset="utf-8">
<title>Signal Safety LLC – Business Card</title>
<link href="https://fonts.googleapis.com/css2?family=Open+Sans:wght@400;700;800&display=swap" rel="stylesheet">
<style>
  :root{
    --page:#dcd7d0;
    --card-top:#f3ece3;
    --card-top-2:#e6ddd1;
    --brand-red:#c9161f;
    --brand-red-dark:#9e0f16;
    --gold:#b8892f;
    --black:#141414;
    --black-2:#262626;
    --text-light:#e4ddd2;
    --text-muted:#cfc6b8;
  }
  *{box-sizing:border-box;margin:0;padding:0}
  html,body{width:1200px;height:1047px;overflow:hidden}
  body{background:var(--page);font-family:"Open Sans",Arial,sans-serif;position:relative}

  .card{
    position:absolute;left:80px;top:226px;width:1040px;height:594px;
    border-radius:24px;overflow:hidden;
    background:linear-gradient(180deg,var(--card-top),var(--card-top-2));
    box-shadow:0 10px 30px rgba(0,0,0,.18);
  }
  .card-shapes{position:absolute;inset:0;width:1040px;height:594px}

  .brand{
    position:absolute;left:0;right:0;top:70px;
    display:flex;flex-direction:column;align-items:center;gap:6px;
  }
  .brand-mark{width:46px;height:46px;background:var(--black-2);margin-bottom:10px}
  .brand-name{
    font-weight:800;color:var(--brand-red);text-align:center;
    font-size:40px;line-height:1.05;letter-spacing:1px;text-transform:uppercase;
  }
  .brand-name small{display:block;font-size:18px;letter-spacing:4px}

  .person{position:absolute;right:568px;top:372px;text-align:right}
  .person-name{color:var(--brand-red);font-weight:700;font-size:34px;letter-spacing:.5px;line-height:1.1}
  .person-role{color:var(--text-muted);font-size:25px;line-height:1.4}

  .divider{position:absolute;left:512px;top:355px;width:2px;height:126px;background:var(--brand-red)}

  .contacts{position:absolute;left:542px;top:350px;list-style:none}
  .contacts li{display:flex;align-items:center;gap:10px;height:36px;color:var(--text-light);font-size:26px}
  .contacts svg{width:22px;height:22px;fill:var(--brand-red);flex:none}

  .gold-rule{position:absolute;left:0;right:0;top:500px;height:4px;background:var(--gold)}
  .footer-band{
    position:absolute;left:0;right:0;top:504px;bottom:0;
    background:linear-gradient(90deg,var(--brand-red-dark),var(--brand-red) 30%,var(--brand-red) 70%,var(--brand-red-dark));
    display:flex;align-items:flex-start;justify-content:center;padding-top:10px;
  }
  .website{color:var(--text-muted);font-size:24px}
</style>
</head>
<body>
  <section class="card">
    <svg class="card-shapes" viewBox="0 0 1040 594" aria-hidden="true">
      <defs>
        <linearGradient id="swooshRed" x1="0" x2="1">
          <stop offset="0" stop-color="#a90f17"/>
          <stop offset=".5" stop-color="#d71a22"/>
          <stop offset="1" stop-color="#a90f17"/>
        </linearGradient>
        <linearGradient id="panelBlack" x1="0" y1="0" x2="0" y2="1">
          <stop offset="0" stop-color="#262626"/>
          <stop offset="1" stop-color="#0e0e0e"/>
        </linearGradient>
      </defs>
      <path d="M0 150 C300 330 740 330 1040 150" fill="none" stroke="var(--gold)" stroke-width="6"/>
      <path d="M0 175 C300 340 740 340 1040 175 L1040 594 L0 594 Z" fill="url(#swooshRed)"/>
      <path d="M0 250 C330 345 710 345 1040 250 L1040 594 L0 594 Z" fill="url(#panelBlack)"/>
    </svg>

    <div class="brand">
      <div class="brand-mark"></div>
      <div class="brand-name">Signal<br>Safety<small>LLC</small></div>
    </div>

    <div class="person">
      <div class="person-name">DANIEL REED</div>
      <div class="person-role">Managing Director</div>
    </div>

    <div class="divider"></div>

    <ul class="contacts">
      <li><svg viewBox="0 0 24 24"><path d="M6.6 10.8a15 15 0 0 0 6.6 6.6l2.2-2.2a1 1 0 0 1 1-.25 11.4 11.4 0 0 0 3.6.57 1 1 0 0 1 1 1V20a1 1 0 0 1-1 1A17 17 0 0 1 3 4a1 1 0 0 1 1-1h3.5a1 1 0 0 1 1 1c0 1.25.2 2.45.57 3.57a1 1 0 0 1-.25 1z"/></svg>123 456 789</li>
      <li><svg viewBox="0 0 24 24"><path d="M6 3h12v5H6zM4 9h16a2 2 0 0 1 2 2v6h-4v4H6v-4H2v-6a2 2 0 0 1 2-2zm4 6v4h8v-4z"/></svg>123 456 789</li>
      <li><svg viewBox="0 0 24 24"><path d="M7 1h10a2 2 0 0 1 2 2v18a2 2 0 0 1-2 2H7a2 2 0 0 1-2-2V3a2 2 0 0 1 2-2zm0 3v14h10V4zm5 15.5a1 1 0 1 0 0 2 1 1 0 0 0 0-2z"/></svg>123 456 789</li>
      <li><svg viewBox="0 0 24 24"><path d="M2 5h20v14H2zm2 2v.5l8 5 8-5V7zm0 3v7h16v-7l-8 5z"/></svg>info@yourmail.com</li>
    </ul>

    <div class="gold-rule"></div>
    <div class="footer-band"><span class="website">www.yourwebsite.com</span></div>
  </section>
</body>
</html>
```